redesign my website bluekeelvoyages.net and make it user friendly

I already have a website, bluekeelvoyages.net, and want a redesign in WordPress with Elementor Pro, using the same text/content. The goal is to improve:

Design quality (colors, fonts, spacing, visual flow)
User experience (easy navigation, clear offers)
Conversion readiness (calls-to-action, trust signals, booking flow)
Technical side (SEO basics, fast speed, full mobile responsiveness)

The site should look modern, clean, fun, engaging, interactive and optimized for speed and usability.

I would like the 11 page to be consolidate dto 6 as follows: Home (main landing, highlights)

Sailboat Trips (all packages, itineraries, pricing)
Boats (fleet details, features, photos)
How It Works (booking process, FAQs, travel info, what to expect)
Blog
Contact Us (form, WhatsApp, phone, etc.)

Target Market(s)

sailboat trip customers for San Blas Islands in Panama

Industry/Entity Type

Travel, Boat Tour Agency

Coding

Coded - Design and coding required

Number of Pages Required

3 page

Font styles to use
Sans Serif
Other font styles liked:
• Oswalg and sans serif

Colors
0054AA
0677BA
7BADD7
CADEEF
E8F1F8
0094D4
00A9DD
6FCCEA
C7EBF8
E9F6FB
FFC000
F8CF3A
FAE287
FDF2CF
FEFAEE
F0912C
F2A743
F7CA91
FBE8D2
FDF5EE

Requirements
Must have
• Home (main landing, highlights) Sailboat Trips (all packages, itineraries, pricing) Boats (fleet details, features, photos) How It Works (booking process, FAQs, travel info, what to expect) Blog (updates, travel tips, inspiration) Contact Us (form, WhatsApp, phone, etc.)
Nice to have
• I want it to look professionla and be very user friendy to entice people to contact me to book boat trips
Should not have
• a store

```html
<!DOCTYPE html>
<html lang="en">
<head>
<meta charset="utf-8">
<title>Blue Keel Voyages – San Blas Sailing</title>
<link href="https://fonts.googleapis.com/css2?family=Oswald:wght@400;500;600&family=Roboto:ital,wght@0,400;0,500;0,700;1,400&display=swap" rel="stylesheet">
<style>
:root{
  --navy:#0054AA;--blue:#0677BA;--sky:#7BADD7;--mist:#CADEEF;--ice:#E8F1F8;
  --teal:#0094D4;--aqua:#00A9DD;--lagoon:#6FCCEA;
  --gold:#FFC000;--sun:#F8CF3A;--cream:#FDF2CF;--orange:#F0912C;--amber:#F2A743;
  --ink:#1b1b1b;--text:#555;--white:#fff;--ring:#2f74c0;
}
*{box-sizing:border-box;margin:0;padding:0}
html,body{width:1200px;height:4412px;overflow:hidden}
body{font-family:"Roboto",Arial,sans-serif;color:var(--text);background:var(--white);position:relative}
.abs{position:absolute}
h1,h2,h3,.oswald{font-family:"Oswald","Arial Narrow",sans-serif;font-weight:500;color:var(--ink)}
.btn{position:absolute;display:flex;align-items:center;justify-content:center;background:linear-gradient(#2f7fd0,#1a5ea8);color:#fff;font-weight:700;font-size:15px;border-radius:4px;box-shadow:0 4px 10px rgba(0,60,140,.3);text-transform:uppercase}
.rule{position:absolute;left:570px;width:60px;height:3px;background:var(--amber)}
.sec-title{position:absolute;left:0;width:1200px;text-align:center;font-size:37px}

/* header */
.topbar{top:0;left:0;width:1200px;height:75px;background:#fff}
.brand{display:flex;align-items:center;gap:10px}
.brand-mark{width:40px;height:40px;border-radius:50%;background:var(--teal)}
.brand-name{font-family:"Oswald",sans-serif;font-weight:500;font-size:21px;color:var(--ink)}
.contact-chip{display:flex;align-items:center;gap:12px}
.chip-icon{width:34px;height:34px;border-radius:50%;background:var(--amber);display:flex;align-items:center;justify-content:center}
.chip-label{font-size:12px;color:#444}
.chip-value{font-size:17px;font-weight:500;color:var(--ink)}
.mainnav{top:75px;left:0;width:1200px;height:48px;background:linear-gradient(#4c96de,#1c66b6)}
.mainnav ul{list-style:none;display:flex;position:absolute;left:120px;top:0;height:48px}
.mainnav li{color:#fff;font-weight:700;font-size:14px;padding:0 22px;display:flex;align-items:center}
.mainnav li.active{background:linear-gradient(#fbd24a,#f2a22c);color:#1b1b1b}

/* hero */
.hero{top:123px;left:0;width:1200px;height:650px;background:linear-gradient(110deg,#0e3b86 0%,#0d5aa6 38%,#13a3c8 62%,#1ec2cf 80%,#0a6eb0 100%)}
.hero h1{position:absolute;left:100px;width:620px;text-align:center;top:100px;color:#fff;font-size:54px;line-height:58px}
.hero .tag{position:absolute;left:100px;width:620px;text-align:center;top:228px;color:var(--sun);font-family:"Oswald",sans-serif;font-size:33px;font-weight:500}
.slide-arrow{position:absolute;width:38px;height:38px;border-radius:50%;display:flex;align-items:center;justify-content:center}

/* tours */
.tour{position:absolute;width:308px;height:308px;border-radius:50%;background:#fff;box-shadow:0 6px 30px rgba(80,130,200,.18);text-align:center;padding:56px 36px 0}
.tour h3{font-size:20px;margin:8px 0 10px}
.tour p{font-size:13px;line-height:21px;color:#666}
.tour.featured{left:445px;top:940px;width:345px;height:345px;box-shadow:none;background:#fff;padding:58px 52px 0;z-index:2}
.tour.featured p{font-size:12.5px;line-height:20px}
.tour.featured .ring{position:absolute;left:0;top:0}

/* boats */
.card{position:absolute;top:1917px;width:431px;height:569px;background:#fff;border-radius:14px;box-shadow:0 6px 24px rgba(0,0,0,.12);padding:14px}
.card .photo{width:403px;height:248px;border-radius:14px}
.pill{display:inline-block;margin:14px 0 0 18px;background:var(--cream);color:var(--orange);font-size:12px;padding:5px 16px;border-radius:14px}
.card h3{font-size:24px;margin:6px 0 0 22px}
.card .lead{font-size:13px;color:#555;margin:12px 0 0 22px}
.card .quote{font-size:13px;line-height:21px;color:#555;margin:16px 22px 0}
.card .info{position:relative;display:inline-flex;margin:16px 0 0 22px;width:118px;height:38px;background:linear-gradient(#2f7fd0,#1a5ea8);color:#fff;font-size:12px;font-weight:700;border-radius:4px;align-items:center;justify-content:center}
.specs{position:absolute;left:36px;right:36px;bottom:14px;border-top:1px solid #e2e2e2;padding-top:12px;display:flex;justify-content:space-between;font-size:14px;color:#333}
.specs span{display:flex;align-items:center;gap:10px}

/* review */
.review{position:absolute;left:210px;width:780px;text-align:center;font-style:italic;font-size:15px;line-height:24px;color:#555}

/* inquiry */
.inquiry{top:3159px;left:0;width:1200px;height:930px;background:linear-gradient(160deg,#3f8ad4,#2f78c6 50%,#3a85cf)}
.field{position:absolute;height:60px;border:2px solid #fff;border-radius:8px;color:#fff;font-size:14px;font-weight:700;padding:0 18px;display:flex;align-items:center;justify-content:space-between}
.checks{position:absolute;color:#fff;font-size:14px;line-height:20px}
.checks div{display:flex;align-items:center;gap:10px}
.checks div::before{content:"";width:11px;height:11px;border:1.5px solid #fff;border-radius:2px}

/* footer */
.footer h3{font-size:21px}
.flinks{position:absolute;font-size:14px;line-height:24px;color:#333;list-style:none}
.flinks li::before{content:"» ";color:var(--amber);margin-right:10px}
.social{position:absolute;top:4352px;width:26px;height:26px;border-radius:50%;background:#eef1f5}
</style>
</head>
<body>

<header class="abs topbar">
  <div class="abs brand" style="left:152px;top:14px"><span class="brand-mark"></span><span class="brand-name">Blue Keel Voyages</span></div>
  <div class="abs contact-chip" style="left:563px;top:18px">
    <span class="chip-icon"><svg width="16" height="12" viewBox="0 0 16 12"><rect x="1" y="1" width="14" height="10" rx="1" fill="none" stroke="#222" stroke-width="1.6"/><path d="M1 1l7 6 7-6" fill="none" stroke="#222" stroke-width="1.6"/></svg></span>
    <div><div class="chip-label">Mail Us</div><div class="chip-value">hello@bluekeelvoyages.net</div></div>
  </div>
  <div class="abs contact-chip" style="left:882px;top:18px">
    <span class="chip-icon"><svg width="16" height="16" viewBox="0 0 24 24"><path d="M6.6 10.8a15 15 0 006.6 6.6l2.2-2.2a1 1 0 011-.25 11.4 11.4 0 003.6.57 1 1 0 011 1V20a1 1 0 01-1 1A17 17 0 013 4a1 1 0 011-1h3.5a1 1 0 011 1c0 1.25.2 2.45.57 3.57a1 1 0 01-.25 1z" fill="#222"/></svg></span>
    <div><div class="chip-label">Call Us Today</div><div class="chip-value">+573005550142</div></div>
  </div>
</header>

<nav class="abs mainnav">
  <ul><li class="active">Home</li><li>Sailboat Trips</li><li>Boats</li><li>How It Works</li><li>Blog</li><li>Contact Us</li></ul>
</nav>

<section class="abs hero" role="img" aria-label="Catamaran anchored in turquoise water beside a sandy San Blas island">
  <h1>San Blas Islands:<br>Panama Sailing Vacations.</h1>
  <div class="tag">Ultimate Beaches &amp; Catamaran Tours</div>
  <div class="btn" style="left:325px;top:291px;width:172px;height:48px">Inquire Now</div>
  <div class="slide-arrow" style="left:368px;top:390px;background:#fff"><svg width="12" height="12" viewBox="0 0 12 12"><path d="M8 1L3 6l5 5" fill="none" stroke="#333" stroke-width="2"/></svg></div>
  <div class="slide-arrow" style="left:416px;top:390px;background:#2f74c0"><svg width="12" height="12" viewBox="0 0 12 12"><path d="M4 1l5 5-5 5" fill="none" stroke="#fff" stroke-width="2"/></svg></div>
  <svg class="abs" style="left:0;top:470px" width="1200" height="180" viewBox="0 0 1200 180" preserveAspectRatio="none">
    <path d="M0 140 C250 40 450 80 650 130 C850 180 1050 130 1200 60 L1200 180 L0 180Z" fill="#fff"/>
    <path d="M0 120 C250 30 450 60 650 110 C850 160 1050 120 1200 50 L1200 70 C1050 145 850 180 650 135 C450 85 250 45 0 140Z" fill="#f4b031"/>
    <path d="M60 110 C280 40 450 60 650 100 C840 140 1040 110 1200 30 L1200 48 C1040 125 840 155 650 118 C450 78 280 55 60 110Z" fill="#2f74c0"/>
  </svg>
</section>

<div class="rule" style="top:845px"></div>
<h2 class="sec-title" style="top:860px">Discover Ultimate Panama Sailing Tours</h2>

<div class="tour" style="left:149px;top:958px">
  <svg width="80" height="56" viewBox="0 0 80 56"><path d="M6 36h68l-8 14H14z" fill="none" stroke="#2f74c0" stroke-width="2.5"/><path d="M20 36V24h30v12M30 24V14h12v10" fill="none" stroke="#f2a743" stroke-width="2.5"/><path d="M2 54c8-4 12 0 20-3s12 2 20-1 12 2 20-1 10 2 16 0" fill="none" stroke="#2f74c0" stroke-width="2"/></svg>
  <h3>Private Charters</h3>
  <p>Sail the beautiful islands and beaches of San Blas on a private all-inclusive catamaran. Enjoy a custom itinerary, friendly crew, and flexible options to fit any budget—perfect for a relaxing escape.</p>
</div>
<div class="tour" style="left:745px;top:958px">
  <svg width="70" height="56" viewBox="0 0 70 56"><path d="M6 34h58l-8 16H14z" fill="none" stroke="#2f74c0" stroke-width="2.5"/><path d="M16 34V22h38v12M26 22V12h18v10M35 12V4" fill="none" stroke="#f2a743" stroke-width="2.5"/></svg>
  <h3>Family Friendly Boat Trips</h3>
  <p>San Blas is perfect for kids, with calm waters, safe snorkeling, and fun island-hopping. Families love the mix of adventure and culture—an ideal way to explore Panama together.</p>
</div>
<div class="tour featured">
  <svg class="ring" width="345" height="345" viewBox="0 0 345 345" aria-hidden="true">
    <path d="M14 140 A160 160 0 0 1 331 140" fill="none" stroke="#2f74c0" stroke-width="7"/>
    <path d="M331 205 A160 160 0 0 1 14 205" fill="none" stroke="#2f74c0" stroke-width="7"/>
  </svg>
  <div style="position:relative">
    <svg width="80" height="52" viewBox="0 0 80 52"><path d="M8 34h64l-10 12H16z" fill="none" stroke="#2f74c0" stroke-width="2.5"/><path d="M18 34l8-14h26l8 14M32 20V10h16v10" fill="none" stroke="#f2a743" stroke-width="2.5"/><path d="M2 50c10-4 16 1 26-2s16 2 26-1 14 2 24 0" fill="none" stroke="#2f74c0" stroke-width="2"/></svg>
    <h3>Shared Charters</h3>
    <p>Share the experience with others for a more affordable alternative to a private charter. Perfect for couples, solo travelers, and small groups—enjoy San Blas beaches, clear waters, great meals, and a relaxed atmosphere with a welcoming crew.</p>
  </div>
</div>

<div class="abs" style="left:0;top:1284px;width:1200px;height:447px;background:linear-gradient(#ffffff 0%,#dfeefb 30%,#8fc3ea 60%,#1f7fc6 78%,#0f5fa8 100%)" role="img" aria-label="Small palm-covered island surrounded by open sea"></div>
<div class="abs oswald" style="left:0;top:1268px;width:1200px;text-align:center;font-size:170px;font-weight:600;color:#fff;letter-spacing:4px;line-height:1;white-space:nowrap;overflow:hidden">BLUE KEEL VOYAGES</div>
<div class="btn" style="left:505px;top:1318px;width:190px;height:50px">Request A Quote</div>

<section class="abs" style="left:0;top:1731px;width:1200px;height:931px;background:linear-gradient(#d8f1fb 0%,#b9e4f3 35%,#e9dfd0 70%,#d9c9b2 100%)" role="img" aria-label="Soft blurred beach and shallow water backdrop"></section>
<div class="rule" style="top:1820px"></div>
<h2 class="sec-title" style="top:1836px">Featured Catamarans</h2>
<svg class="abs" style="left:60px;top:2190px" width="20" height="28" viewBox="0 0 20 28"><path d="M16 2L4 14l12 12" fill="none" stroke="#f2a743" stroke-width="4"/></svg>
<svg class="abs" style="left:1116px;top:2190px" width="20" height="28" viewBox="0 0 20 28"><path d="M4 2l12 12L4 26" fill="none" stroke="#f2a743" stroke-width="4"/></svg>

<article class="card" style="left:144px">
  <div class="photo" style="background:linear-gradient(135deg,#0f8aa8,#4fd0d8 55%,#1a6f9c)" role="img" aria-label="Aerial view of a white catamaran over turquoise shallows"></div>
  <span class="pill">Catamaran</span>
  <h3>Marisol 42</h3>
  <p class="lead">Service that exceeds all expectations!</p>
  <p class="quote">“We started as strangers and left as friends! The crew made sure everyone felt welcome, and every moment was filled with fun and laughter.”</p>
  <span class="info">INFO &amp; PRICE</span>
  <div class="specs"><span>▙ 42 ft</span><span>⛴ 3 cabin</span><span>👥 8 Guest</span></div>
</article>
<article class="card" style="left:625px">
  <div class="photo" style="background:linear-gradient(135deg,#1f8fb8,#6fd6d8 45%,#2e8a5a 70%,#1a6f9c)" role="img" aria-label="Aerial view of a catamaran anchored beside a palm island"></div>
  <span class="pill">Catamaran</span>
  <h3>Coralina 55F</h3>
  <p class="lead">Luxury and elegance on water!</p>
  <p class="quote">“It was like having our own private island, but with the luxury of a floating home. Every detail was taken care of, and we felt like VIPs the entire time!”</p>
  <span class="info">INFO &amp; PRICE</span>
  <div class="specs"><span>▙ 42 ft</span><span>⛴ 3 cabin</span><span>👥 8 Guest</span></div>
</article>
<div class="btn" style="left:486px;top:2522px;width:230px;height:50px">See All Boats &amp; Prices</div>

<div class="rule" style="top:2733px"></div>
<h2 class="sec-title" style="top:2748px">What They Say</h2>
<div class="abs" style="left:0;top:2840px;width:1200px;text-align:center;color:var(--amber);font-size:16px;letter-spacing:2px">★★★★★</div>
<div class="abs oswald" style="left:870px;top:2940px;font-size:190px;color:#e6e6e6;line-height:1">”</div>
<p class="review" style="top:2870px">Everything was absolutely great — from the transfer to the boat crew, the food, and the islands we visited. We really enjoyed the whole experience. The only thing we regret is not having more time to extend the trip in San Blas. We booked the Alba, the boat is spacious and very confortable. The captain Mateo and the chef Elena. Were very professional, friendly and have a lot of knowledge of the San Blas and sailing. They took good care of us and made the trip even better. Chef Elena cooked amazing food!<br><br>Thanks again for the great organization, and we definitely hope to come back in the future!</p>
<svg class="abs" style="left:60px;top:2938px" width="20" height="28" viewBox="0 0 20 28"><path d="M16 2L4 14l12 12" fill="none" stroke="#f2a743" stroke-width="4"/></svg>
<svg class="abs" style="left:1116px;top:2938px" width="20" height="28" viewBox="0 0 20 28"><path d="M4 2l12 12L4 26" fill="none" stroke="#f2a743" stroke-width="4"/></svg>

<section class="abs inquiry" role="img" aria-label="Blue-tinted catamaran deck backdrop">
  <div class="rule" style="top:96px;background:var(--sun)"></div>
  <h2 class="sec-title" style="top:112px;color:#fff">Make An Inquiry Now</h2>
  <div class="field" style="left:143px;top:184px;width:296px">Name</div>
  <div class="field" style="left:452px;top:184px;width:296px">Email</div>
  <div class="field" style="left:761px;top:184px;width:296px">Whatsapp Number</div>
  <div class="field" style="left:143px;top:256px;width:296px">Number of Passengers<span>⇕</span></div>
  <div class="field" style="left:452px;top:256px;width:296px">Number Of Days<span>⇕</span></div>
  <div class="field" style="left:761px;top:256px;width:296px">Date<span>▦</span></div>
  <div class="abs" style="left:143px;top:335px;color:#fff;font-size:14px;font-weight:700">What type of experience are you looking for? (Check all that apply)</div>
  <div class="checks" style="left:143px;top:380px"><div>Relaxing and disconnected</div><div>Island-hopping adventure</div><div>Snorkeling &amp; marine life</div><div>Cultural exchange with the Guna people</div></div>
  <div class="checks" style="left:517px;top:380px"><div>Family-friendly</div><div>Romantic getaway</div><div>Food &amp; drink-focused</div></div>
  <div class="checks" style="left:780px;top:380px"><div>Sailing-focused</div><div>Budget-friendly</div><div>Luxury experience</div></div>
  <div class="field" style="left:143px;top:480px;width:914px;height:142px;align-items:flex-start;padding-top:16px">Message</div>
  <div class="abs" style="left:486px;top:641px;width:230px;height:50px;background:#fff;border-radius:4px;color:#1b1b1b;font-weight:700;font-size:15px;display:flex;align-items:center;justify-content:center">SEE ALL BOATS &amp; PRICES</div>
  <svg class="abs" style="left:0;top:760px" width="1200" height="170" viewBox="0 0 1200 170" preserveAspectRatio="none">
    <path d="M0 50 C250 -10 450 30 650 90 C850 150 1050 110 1200 30 L1200 170 L0 170Z" fill="#fff"/>
    <path d="M0 40 C250 -20 450 20 650 80 C850 140 1050 100 1200 20 L1200 40 C1050 125 850 165 650 105 C450 45 250 5 0 60Z" fill="#f4b031"/>
    <path d="M0 28 C250 -25 450 10 650 62 C850 118 1050 85 1200 8 L1200 24 C1050 100 850 135 650 80 C450 25 250 -8 0 42Z" fill="#2f74c0"/>
  </svg>
</section>

<footer class="footer">
  <div class="abs brand" style="left:143px;top:4150px"><span class="brand-mark"></span><span class="brand-name" style="font-size:24px">Blue Keel Voyages</span></div>
  <p class="abs" style="left:143px;top:4214px;width:350px;font-size:13px;line-height:20px;color:#333">Discover unforgettable catamaran and sailboat adventures in Guna Yala (San Blas), Panama. We Blue Keel Voyages LLC offers all-inclusive island-hopping, snorkeling, and immersive cultural experiences—trusted by travelers worldwide.</p>
  <h3 class="abs" style="left:568px;top:4130px">Get In Touch</h3>
  <div class="abs contact-chip" style="left:568px;top:4180px"><span class="chip-icon" style="width:28px;height:28px"><svg width="13" height="13" viewBox="0 0 24 24"><path d="M6.6 10.8a15 15 0 006.6 6.6l2.2-2.2a1 1 0 011-.25 11.4 11.4 0 003.6.57 1 1 0 011 1V20a1 1 0 01-1 1A17 17 0 013 4a1 1 0 011-1h3.5a1 1 0 011 1c0 1.25.2 2.45.57 3.57a1 1 0 01-.25 1z" fill="#222"/></svg></span><span style="font-size:14px;color:#333">+573005550142</span></div>
  <div class="abs contact-chip" style="left:568px;top:4232px"><span class="chip-icon" style="width:28px;height:28px"><svg width="13" height="10" viewBox="0 0 16 12"><rect x="1" y="1" width="14" height="10" rx="1" fill="none" stroke="#222" stroke-width="1.6"/><path d="M1 1l7 6 7-6" fill="none" stroke="#222" stroke-width="1.6"/></svg></span><span style="font-size:14px;color:#333">hello@bluekeelvoyages.net</span></div>
  <h3 class="abs" style="left:827px;top:4130px">Quick Links</h3>
  <ul class="flinks" style="left:830px;top:4172px"><li>Home</li><li>Sailboat Trips</li><li>Boats</li></ul>
  <ul class="flinks" style="left:955px;top:4172px"><li>How It Works</li><li>Blog</li><li>Contact Us</li></ul>
  <div class="abs" style="left:143px;top:4328px;width:914px;height:1px;background:#ddd"></div>
  <span class="social" style="left:146px"></span>
  <span class="social" style="left:177px;background:#2f74c0"></span>
  <span class="social" style="left:208px"></span>
  <div class="abs" style="left:0;top:4357px;width:1200px;text-align:center;font-size:13px;color:#333">© Copyrights 2025 | All Rights Reserved</div>
  <div class="abs" style="left:988px;top:4347px;width:68px;height:32px;border:1px solid #ccc;border-radius:4px;display:flex;align-items:center;justify-content:center;gap:6px;font-size:13px;color:#333"><span style="width:16px;height:12px;background:#c8102e;display:inline-block"></span>Eng</div>
</footer>

</body>
</html>
```